Design a single page Shopify store web page

We are looking to have a page designed for a single page Shopify store with 2 products. We already have a basic structure that we like, though we are open to suggestions. We are looking for somebody to provide a design/color scheme that we can then implement using Shopify's templating system. We can handle the implementation(HTML / CSS / jS) as we already have 2 web developers on the team, but have not been able to find a design we liked.

The job would consist of providing a mockup (photoshop or otherwise) and any vector graphics you choose to create for the site (we can provide product photos and other images).

You can also look at http://brickdune.com.au for some of our design direction we have used so far

Target Market(s)

Young Australian Males (18 - 49)

Industry/Entity Type

Store

Number of Pages Required

1 page

Font styles to use
Serif
Sans Serif

Requirements
Must have
• Single Page Design
• E-commerce Product Purchase
• Manly (whatever interpretation of that you have)

```html
<!DOCTYPE html>
<html lang="en">
<head>
<meta charset="utf-8">
<title>FAQ – Brick Dune</title>
<link href="https://fonts.googleapis.com/css2?family=Economica:wght@400;700&family=Open+Sans:wght@300;400&display=swap" rel="stylesheet">
<style>
  :root {
    --bg: #0e0e0e;
    --top-band: #0c1512;
    --heading: #f2f2f2;
    --body-text: #d6d6d6;
    --rule: #cfcfcf;
    --brand: #a9a9a9;
    --muted: #b0b0b0;
  }
  * { margin: 0; padding: 0; box-sizing: border-box; }
  html, body {
    width: 1200px;
    height: 897px;
    overflow: hidden;
    background: var(--bg);
  }
  .page {
    position: relative;
    width: 1200px;
    height: 897px;
    background: var(--bg);
    border-top: 4px solid var(--top-band);
  }
  .faq-title {
    position: absolute;
    top: 46px;
    left: 0;
    width: 1200px;
    text-align: center;
    font-family: "Economica", sans-serif;
    font-weight: 700;
    font-size: 62px;
    line-height: 1;
    color: var(--heading);
    letter-spacing: 1px;
  }
  .faq-item {
    position: absolute;
    width: 238px;
  }
  .faq-question {
    font-family: "Economica", sans-serif;
    font-weight: 400;
    font-size: 27px;
    line-height: 31px;
    color: var(--heading);
    letter-spacing: 0.5px;
  }
  .faq-question.narrow { width: 200px; }
  .faq-answer {
    margin-top: 3px;
    padding-left: 2px;
    font-family: "Open Sans", sans-serif;
    font-size: 12.2px;
    line-height: 20.6px;
    color: var(--body-text);
    width: 226px;
  }
  .faq-answer.single { margin-top: 8px; }
  .footer-rule {
    position: absolute;
    top: 748px;
    left: 89px;
    width: 1021px;
    height: 2px;
    background: var(--rule);
  }
  .footer-brand {
    position: absolute;
    top: 764px;
    left: 197px;
    font-family: "Economica", sans-serif;
    font-weight: 700;
    font-size: 30px;
    line-height: 34px;
    color: var(--brand);
  }
  .copyright {
    position: absolute;
    top: 774px;
    right: 198px;
    font-family: "Open Sans", sans-serif;
    font-weight: 300;
    font-size: 12px;
    color: var(--muted);
  }
</style>
</head>
<body>
<main class="page">
  <h1 class="faq-title">FAQ</h1>

  <section class="faq-item" style="left:217px; top:144px;">
    <h2 class="faq-question">What is Brick Dune?</h2>
    <p class="faq-answer single">Lorem ipsum dolor sizt amet, consect-etur adipisicing elit. Autem eveniet vel tempore consequuntur. Officia eos, animi quos sequi quas accusantium possimus alias esse nulla. Similique</p>
  </section>
  <section class="faq-item" style="left:494px; top:144px;">
    <h2 class="faq-question">Return Policy</h2>
    <p class="faq-answer single">Lorem ipsum dolor sizt amet, consect-etur adipisicing elit. Autem eveniet vel tempore consequuntur. Officia eos, animi quos sequi quas accusantium possimus alias esse nulla. Similique</p>
  </section>
  <section class="faq-item" style="left:768px; top:144px;">
    <h2 class="faq-question">Shipping Policy</h2>
    <p class="faq-answer single">Lorem ipsum dolor sizt amet, consect-etur adipisicing elit. Autem eveniet vel tempore consequuntur. Officia eos, animi quos sequi quas accusantium possimus alias esse nulla. Similique</p>
  </section>

  <section class="faq-item" style="left:217px; top:324px;">
    <h2 class="faq-question">What do I get with my Brick Dune plan?</h2>
    <p class="faq-answer">Lorem ipsum dolor sizt amet, consect-etur adipisicing elit. Autem eveniet vel tempore consequuntur. Officia eos, animi quos sequi quas accusantium possimus alias esse nulla. Similique</p>
  </section>
  <section class="faq-item" style="left:496px; top:324px;">
    <h2 class="faq-question">What is your Satisfaction Guarantee?</h2>
    <p class="faq-answer">Lorem ipsum dolor sizt amet, consect-etur adipisicing elit. Autem eveniet vel tempore consequuntur. Officia eos, animi quos sequi quas accusantium possimus alias esse nulla. Similique</p>
  </section>
  <section class="faq-item" style="left:769px; top:324px;">
    <h2 class="faq-question narrow">What brands do you Stock?</h2>
    <p class="faq-answer">Lorem ipsum dolor sizt amet, consect-etur adipisicing elit. Autem eveniet vel tempore consequuntur. Officia eos, animi quos sequi quas accusantium possimus alias esse nulla. Similique</p>
  </section>

  <section class="faq-item" style="left:217px; top:529px;">
    <h2 class="faq-question">What is your cancelation policy?</h2>
    <p class="faq-answer">Lorem ipsum dolor sizt amet, consect-etur adipisicing elit. Autem eveniet vel tempore consequuntur. Officia eos, animi quos sequi quas accusantium possimus alias esse nulla. Similique</p>
  </section>
  <section class="faq-item" style="left:496px; top:529px;">
    <h2 class="faq-question">How does payment work?</h2>
    <p class="faq-answer single">Lorem ipsum dolor sizt amet, consect-etur adipisicing elit. Autem eveniet vel tempore consequuntur. Officia eos, animi quos sequi quas accusantium possimus alias esse nulla. Similique</p>
  </section>
  <section class="faq-item" style="left:769px; top:529px;">
    <h2 class="faq-question">What about sizing?</h2>
    <p class="faq-answer single">Lorem ipsum dolor sizt amet, consect-etur adipisicing elit. Autem eveniet vel tempore consequuntur. Officia eos, animi quos sequi quas accusantium possimus alias esse nulla. Similique</p>
  </section>

  <footer>
    <div class="footer-rule"></div>
    <p class="footer-brand">Brick Dune</p>
    <p class="copyright">Copyright Lord Halvern 2014</p>
  </footer>
</main>
</body>
</html>
```